Hollow Thicket, a 3d voxel survival video game needs a card for gaming conventions

I am the lead developer for Hollow Thicket http://www.HollowThicket.example and need a business card to hand out at an indie gaming convention
The card would need to include the game name, website url, my name, position (Lead Developer), e-mail and phone number
The game is a 3d, voxel (with smooth terrain) based survival game with guns and wildlife. The main icon of the game would likely be a grizzly bear but I am willing to accept other designs too.
Attached is a media kit for the game with some images you can use but don't have to its just what little art I can provide. Anything on the website or from the video game can also be used. unrelated art can also be used.
Target Market(s)
Indie Developers/publishers at conferences
Industry/Entity Type
Games
Contact Information for Business Card
Name: Corin Waldrick
Position: Lead Developer
E-mail: Pale_Kettle@mailbox.example
Phone number: 555-372-1186

```html
<!DOCTYPE html>
<html lang="en">
<head>
<meta charset="utf-8">
<title>Hollow Thicket – Business Card</title>
<link href="https://fonts.googleapis.com/css2?family=Open+Sans:wght@400;600;700&display=swap" rel="stylesheet">
<style>
  :root {
    --backdrop: #ecebe8;
    --kraft: #c8a47a;
    --kraft-light: #d2b088;
    --kraft-dark: #bd9767;
    --ink: #1c1712;
    --brand-red: #b3362a;
    --bear-brown: #7a5a3c;
    --bear-dark: #4e3825;
  }
  * { box-sizing: border-box; margin: 0; padding: 0; }
  html, body {
    width: 1200px;
    height: 900px;
    overflow: hidden;
    background: var(--backdrop);
    font-family: "Open Sans", Arial, sans-serif;
  }
  .canvas { position: relative; width: 1200px; height: 900px; }
  .card {
    position: absolute;
    background: radial-gradient(ellipse at 40% 35%, var(--kraft-light), var(--kraft) 55%, var(--kraft-dark));
    box-shadow: 0 4px 14px rgba(0,0,0,0.18);
  }
  .card--front { left: 238px; top: 62px; width: 555px; height: 341px; }
  .card--back  { left: 457px; top: 518px; width: 560px; height: 342px; }

  .mascot-photo {
    position: absolute;
    left: 0; top: 58px;
    width: 225px; height: 283px;
    border-radius: 60px 90px 0 0;
    background: radial-gradient(ellipse at 60% 40%, var(--bear-brown), var(--bear-dark) 85%);
  }
  .wordmark {
    font-family: "Open Sans", Arial, sans-serif;
    font-weight: 700;
    color: var(--brand-red);
    text-transform: uppercase;
    line-height: 1.05;
    letter-spacing: 2px;
  }
  .card--front .wordmark {
    position: absolute;
    left: 262px; top: 44px;
    font-size: 42px;
  }
  .card--back .wordmark {
    position: absolute;
    left: 0; right: 0; top: 112px;
    text-align: center;
    font-size: 54px;
  }
  .contact-name {
    position: absolute; left: 257px; top: 188px;
    font-size: 18px; font-weight: 600; color: var(--ink);
  }
  .contact-role {
    position: absolute; left: 257px; top: 210px;
    font-size: 14.5px; color: var(--ink);
  }
  .contact-list {
    position: absolute; left: 257px; top: 259px;
    list-style: none;
    font-size: 14.5px; color: var(--ink);
  }
  .contact-list li { display: flex; align-items: center; height: 21px; white-space: nowrap; }
  .contact-list svg { width: 11px; height: 11px; margin-right: 9px; flex: none; }
</style>
</head>
<body>
<main class="canvas">
  <section class="card card--front">
    <div class="mascot-photo" role="img" aria-label="Photograph of a standing grizzly bear"></div>
    <div class="wordmark">Hollow<br>Thicket</div>
    <p class="contact-name">Corin Waldrick</p>
    <p class="contact-role">Lead Developer</p>
    <ul class="contact-list">
      <li>
        <svg viewBox="0 0 24 24" aria-hidden="true"><path fill="var(--ink)" d="M6.6 10.8a15.1 15.1 0 0 0 6.6 6.6l2.2-2.2a1 1 0 0 1 1-.25 11.4 11.4 0 0 0 3.6.57 1 1 0 0 1 1 1V20a1 1 0 0 1-1 1A17 17 0 0 1 3 4a1 1 0 0 1 1-1h3.5a1 1 0 0 1 1 1c0 1.25.2 2.45.57 3.57a1 1 0 0 1-.25 1z"/></svg>
        555-372-1186
      </li>
      <li>
        <svg viewBox="0 0 24 24" aria-hidden="true"><rect x="2" y="5" width="20" height="14" fill="var(--ink)"/><path d="M3 6l9 6.5L21 6" fill="none" stroke="var(--kraft)" stroke-width="2"/></svg>
        Pale_Kettle@mailbox.example
      </li>
      <li>
        <svg viewBox="0 0 24 24" aria-hidden="true"><g fill="none" stroke="var(--ink)" stroke-width="2"><circle cx="12" cy="12" r="10"/><ellipse cx="12" cy="12" rx="4.5" ry="10"/><path d="M2 12h20"/></g></svg>
        www.HollowThicket.example
      </li>
    </ul>
  </section>

  <section class="card card--back">
    <div class="wordmark">Hollow<br>Thicket</div>
  </section>
</main>
</body>
</html>
```